Design a modern, classy & professional business card for an online real estate agency, specializing in medium-luxury properties in Thailand and later in Singapore and UK.

Possible design ideas so far: (not essential)

- curved corner(s) to the card, white on front & turquoise on back or visa versa.

- front of card - clear and simple, company name in metallic grey/monochrome, logo graphic & company name on front in spot UV or embossed/debossed effect.

- back of card - large, close-cropped, 'ghost' patterns of the C-shaped curves of logo, or company name repeated on back of card in spot UV.

Target Market(s)

- young to middle-aged professionals mainly (but ideally should design should suit all)

- UK, US,EU,AUS & ASIAN mainly (but ideally should design should suit all countries)

Industry/Entity Type

Real Estate

Requirements
Must have
• THEME:
- Luxurious & Modern
- Clean & striking
- Unique & creative

INFO:
- Logo & company name on front
- Contact details on back:

Tobias Hennlund
Managing Director

www.velmontestates.asia
www.velmontestates.co.uk

Tel: 083-274-6159
email: tobias@velmontestates.asia

(contact details can be displayed in any order as suites design.)

Nice to have
• - curved corner(s) to the card, white on front & turquoise on back or visa versa.

Should not have
• - No generic images of properties, palm trees/coconut trees etc.

- No other other bold colors, except for main turquoise, grey, metallic white & black theme.

- No obvious business card templates

```html
<!DOCTYPE html>
<html lang="en">
<head>
<meta charset="utf-8">
<title>Velmont Estates – Business Card</title>
<link href="https://fonts.googleapis.com/css2?family=Cormorant+Garamond:wght@500&family=Roboto+Condensed:wght@400;700&display=swap" rel="stylesheet">
<style>
  :root {
    --teal: #5fbcb8;
    --teal-deep: #3f9e9a;
    --teal-light: #8fd3cf;
    --grey: #8a8a8a;
    --grey-dark: #6b6b6b;
    --ink: #1f1f1f;
    --white: #ffffff;
    --paper-shade: #eeeeee;
    --backdrop: #e4e4e2;
  }
  * { margin: 0; padding: 0; box-sizing: border-box; }
  html, body { width: 1200px; height: 913px; overflow: hidden; }
  body {
    background: var(--backdrop);
    position: relative;
    font-family: "Roboto Condensed", sans-serif;
  }
  .card {
    position: absolute;
    width: 520px;
    height: 300px;
    border-radius: 22px;
    overflow: hidden;
    background: var(--white);
    box-shadow: 0 10px 28px rgba(0,0,0,0.18);
  }
  .card--front { left: 70px; top: 130px; }
  .card--back { left: 610px; top: 480px; }

  .front-texture {
    position: absolute; inset: 0;
    background: radial-gradient(ellipse at 50% 50%, var(--white) 0%, var(--paper-shade) 100%);
  }
  .brand {
    position: absolute;
    display: flex;
    align-items: center;
    gap: 14px;
  }
  .brand__square { background: var(--teal); flex: none; }
  .brand__name {
    font-family: "Cormorant Garamond", serif;
    font-weight: 500;
    color: var(--grey);
    line-height: 1;
    white-space: nowrap;
  }
  .card--front .brand { left: 90px; top: 108px; }
  .card--front .brand__square { width: 84px; height: 84px; }
  .card--front .brand__name { font-size: 50px; }

  .card--back .brand { left: 150px; top: 16px; }
  .card--back .brand__square { width: 62px; height: 62px; }
  .card--back .brand__name { font-size: 36px; }

  .back-shape { position: absolute; inset: 0; }
  .holder {
    position: absolute;
    right: 34px;
    top: 86px;
    text-align: right;
    line-height: 1.1;
  }
  .holder__name { color: var(--teal); font-weight: 700; font-size: 17px; }
  .holder__role { color: var(--grey-dark); font-size: 12px; margin-top: 3px; }

  .contacts {
    position: absolute;
    left: 22px;
    bottom: 18px;
    list-style: none;
  }
  .contacts li {
    display: flex;
    align-items: center;
    gap: 10px;
    color: var(--ink);
    font-weight: 700;
    font-size: 14px;
    line-height: 1;
    margin-top: 7px;
  }
  .contacts li:first-child { font-size: 16px; margin-top: 0; }
  .contacts svg { width: 16px; height: 16px; flex: none; }
</style>
</head>
<body>

<section class="card card--front" aria-label="Card front">
  <div class="front-texture" role="img" aria-label="Faint ring pattern in spot UV across the card"></div>
  <div class="brand">
    <span class="brand__square"></span>
    <span class="brand__name">Velmont Estates</span>
  </div>
</section>

<section class="card card--back" aria-label="Card back">
  <svg class="back-shape" viewBox="0 0 520 300" preserveAspectRatio="none" aria-hidden="true">
    <defs>
      <linearGradient id="tealFill" x1="0" y1="0" x2="0" y2="1">
        <stop offset="0" stop-color="var(--teal-light)"/>
        <stop offset="1" stop-color="var(--teal-deep)"/>
      </linearGradient>
    </defs>
    <path d="M0,138 C150,193 360,183 520,138 L520,300 L0,300 Z" fill="url(#tealFill)"/>
    <path d="M0,130 C150,185 360,175 520,130" fill="none" stroke="var(--grey-dark)" stroke-width="5"/>
  </svg>

  <div class="brand">
    <span class="brand__square"></span>
    <span class="brand__name">Velmont Estates</span>
  </div>

  <div class="holder">
    <p class="holder__name">Tobias Hennlund</p>
    <p class="holder__role">Managing Director</p>
  </div>

  <ul class="contacts">
    <li>
      <svg viewBox="0 0 16 16" aria-hidden="true"><path d="M3 3h3l1 3-2 1a8 8 0 0 0 4 4l1-2 3 1v3c-6 0-10-4-10-10z" fill="var(--white)"/></svg>
      083-274-6159
    </li>
    <li>
      <svg viewBox="0 0 16 16" aria-hidden="true"><rect x="1" y="3.5" width="14" height="9" fill="var(--white)"/><path d="M1 3.5l7 5 7-5" fill="none" stroke="var(--teal-deep)" stroke-width="1.2"/></svg>
      tobias@velmontestates.asia
    </li>
    <li>
      <svg viewBox="0 0 16 16" aria-hidden="true"><g fill="none" stroke="var(--white)" stroke-width="1.3"><circle cx="8" cy="8" r="6.5"/><ellipse cx="8" cy="8" rx="3" ry="6.5"/><path d="M1.5 8h13"/></g></svg>
      www.velmontestates.asia
    </li>
    <li>
      <svg viewBox="0 0 16 16" aria-hidden="true"></svg>
      www.velmontestates.co.uk
    </li>
  </ul>
</section>

</body>
</html>
```